Redesign This Psychology Website

We would like a slight redesign of this successful psychology (relationship counselling) website:

www.TheKelvaleClinic.com.au

We are updating the website, and we'd like a slight refresh of the design and style.

Please keep to very similar colours, and use the same logo. We're looking for around 10 page templates, however the main one is the home page.

Keep in mind, this website already converts quite well, so we want a new, fresh design in keeping with this one. Please don't bother designing something too extremely different.

thanks :)

Target Market(s)

couples who are looking for relationship counselling. Men and women, 25 - 70, across Australia

Industry/Entity Type

Psychology

Number of Pages Required

5+ page

Font styles to use
Sans Serif

Colors
87cfc6
b7a5cd
ec1f27
ffffff
cee9f5

Requirements
Must have
• a similar look to the current design, just looking for a slight refresh.
• Search bar
• Areas for lots of photos
• same logo
• lots of content areas
Nice to have
• great content areas, where we can display a lot of content and our areas.
Should not have
• no colors like orange, etc.
• should not have a totally different feel.

```html
<!DOCTYPE html>
<html lang="en">
<head>
<meta charset="utf-8">
<title>The Kelvale Clinic – Relationship &amp; Marriage Counselling</title>
<link href="https://fonts.googleapis.com/css2?family=Lato:wght@300;400;700;900&display=swap" rel="stylesheet">
<style>
:root{
  --teal:#87cfc6;
  --teal-dark:#5fb3aa;
  --red:#ec1f27;
  --lilac:#b7a5cd;
  --sky:#cee9f5;
  --white:#ffffff;
  --ink:#222222;
  --text:#555555;
  --muted:#9a9a9a;
  --line:#e4e4e4;
  --field:#eceff1;
  --footer:#1b1b1b;
  --footer-line:#333333;
}
*{box-sizing:border-box;margin:0;padding:0}
html,body{width:1200px;height:2752px;overflow:hidden}
body{font-family:'Lato',Arial,sans-serif;color:var(--text);background:var(--white);position:relative}
a{color:inherit;text-decoration:none}
.abs{position:absolute}

/* header */
.site-header{position:absolute;left:0;top:0;width:1200px;height:134px;background:var(--white)}
.brand{position:absolute;left:88px;top:34px;display:flex;align-items:center;gap:14px}
.brand-mark{width:44px;height:44px;border-radius:50%;background:var(--teal-dark)}
.brand-name{font-size:34px;font-weight:400;color:var(--teal-dark);line-height:1}
.brand-tag{font-size:15px;color:var(--teal-dark);margin-top:6px}
.top-links{position:absolute;right:88px;top:23px;display:flex;gap:20px;font-size:12.5px;color:var(--ink);letter-spacing:.3px}
.phone{position:absolute;left:674px;top:72px;font-size:19px;font-weight:700;color:var(--red);display:flex;align-items:center;gap:8px}
.search{position:absolute;left:840px;top:62px;width:272px;height:46px;display:flex}
.search-field{flex:1;background:var(--field);font-size:12px;color:var(--ink);padding:16px 30px}
.search-btn{width:52px;background:var(--red);display:flex;align-items:center;justify-content:center}

.main-nav{position:absolute;left:0;top:134px;width:1200px;height:66px;background:var(--teal);display:flex;align-items:center;padding-left:92px;gap:42px;font-size:13.5px;color:var(--white);letter-spacing:.4px}

/* hero */
.hero{position:absolute;left:0;top:200px;width:1200px;height:420px;background:linear-gradient(100deg,#b8a07a 0%,#d9cdb8 30%,#c9b59a 55%,#6f7f5a 85%,#9aa580 100%)}
.finder{position:absolute;left:800px;top:248px;width:312px;height:328px;background:var(--teal)}
.finder-title{height:52px;background:var(--red);color:var(--white);font-size:16.5px;font-weight:700;display:flex;align-items:center;justify-content:center;letter-spacing:.3px}
.finder-body{padding:14px 10px}
.finder-field{height:43px;background:var(--white);border-radius:3px;font-size:13.5px;color:var(--ink);padding:0 30px;display:flex;align-items:center;justify-content:space-between;margin-bottom:10px}
.finder-or{text-align:center;font-size:13px;color:var(--ink);margin:10px 0 12px}
.finder-btn{height:43px;background:var(--red);border-radius:3px;color:var(--white);font-size:15px;font-weight:700;display:flex;align-items:center;justify-content:center}

/* intro */
.intro-title{position:absolute;left:86px;top:680px;font-size:24px;font-weight:700;color:var(--ink);line-height:1.5;letter-spacing:.3px}
.intro-copy{position:absolute;left:86px;top:760px;width:500px;font-size:12px;line-height:1.75;color:var(--text)}
.intro-copy p{margin-bottom:20px}
.btn-teal{position:absolute;left:86px;top:960px;width:120px;height:42px;background:var(--teal);color:var(--white);font-size:14px;font-weight:700;display:flex;align-items:center;justify-content:center}
.video{position:absolute;left:642px;top:680px;width:470px;height:282px;background:#111}
.video-frame{position:absolute;left:0;top:26px;width:470px;height:232px;background:linear-gradient(90deg,#5e7c95 0%,#a98472 45%,#c4594a 100%)}
.video-caption{position:absolute;left:6px;top:210px;width:240px;height:34px;background:rgba(255,255,255,.85);font-size:13px;color:#333;padding:4px 8px;line-height:1.2}
.video-caption small{display:block;font-size:8px;color:#666}
.play{position:absolute;left:214px;top:118px}

/* services */
.services{position:absolute;left:0;top:1073px;width:1200px;height:600px;background:linear-gradient(180deg,#777 0%,#6a6a6a 100%)}
.section-title{position:absolute;left:0;width:1200px;text-align:center;font-size:31px;font-weight:400;letter-spacing:.5px}
.service-card{position:absolute;top:1216px;width:249px;height:372px;background:var(--white);text-align:center}
.service-photo{height:189px}
.service-card h3{font-size:14px;font-weight:400;color:var(--ink);line-height:1.35;margin-top:20px;letter-spacing:.3px}
.service-card p{font-size:11.5px;line-height:1.6;color:var(--text);padding:8px 16px 0;height:84px}
.service-card .more{font-size:12px;color:var(--ink);margin-top:14px;display:block}

/* news */
.news-card{position:absolute;top:1812px;width:321px;height:435px;background:var(--white);border:1px solid var(--line)}
.news-photo{height:228px;position:relative}
.date{position:absolute;right:0;bottom:-22px;width:56px;height:64px;color:var(--white);text-align:center;font-size:12px;line-height:1.1;padding-top:6px}
.date b{display:block;font-size:26px;font-weight:400}
.date.teal{background:var(--teal)} .date.red{background:var(--red)}
.news-card h4{font-size:15px;font-weight:400;color:var(--ink);line-height:1.35;padding:12px 20px 0;width:270px}
.news-card h4.hot{color:var(--red)}
.news-card p{font-size:12px;line-height:1.75;color:var(--muted);padding:18px 20px 0;height:122px}
.news-card .more{font-size:12.5px;color:var(--ink);padding:0 20px;display:block;margin-top:12px}
.news-card .more.hot{color:var(--red)}

/* footer */
.site-footer{position:absolute;left:0;top:2337px;width:1200px;height:415px;background:var(--footer);color:var(--white)}
.foot-col{position:absolute;top:40px}
.foot-col h5{font-size:17px;font-weight:700;letter-spacing:.4px;padding-bottom:10px;border-bottom:1px solid #555;width:230px}
.contact-line{display:flex;align-items:center;gap:22px;font-size:13px;margin-top:26px}
.field{width:238px;height:38px;border:1px solid #555;margin-top:12px;font-size:12px;color:#999;padding:11px 12px}
.field.tall{height:62px}
.send{width:100px;height:32px;background:var(--red);font-size:12px;display:flex;align-items:center;justify-content:center;margin-top:16px}
.news-note{font-size:12px;line-height:1.6;margin-top:16px;width:260px}
.subscribe{display:flex;margin-top:28px;width:268px;height:48px}
.subscribe-field{flex:1;background:var(--white);color:var(--ink);font-size:12px;padding:17px 20px}
.subscribe-btn{width:56px;background:var(--red);display:flex;align-items:center;justify-content:center}
.social{position:absolute;left:86px;top:252px;display:flex;gap:12px}
.social span{width:20px;height:20px;border-radius:50%;background:#777}
.bottom-bar{position:absolute;left:0;top:325px;width:1200px;height:90px;border-top:1px solid var(--footer-line);font-size:10.5px;display:flex;align-items:center;justify-content:space-between;padding:0 88px 0 86px}
.legal{display:flex;gap:10px}
</style>
</head>
<body>

<header class="site-header">
  <div class="brand">
    <span class="brand-mark"></span>
    <div>
      <div class="brand-name">The Kelvale Clinic</div>
      <div class="brand-tag">helping you create loving relationships</div>
    </div>
  </div>
  <nav class="top-links"><a>HOME</a><a>ABOUT</a><a>RESOURCES</a><a>BLOG</a><a>SHOP</a><a>CART</a></nav>
  <div class="phone">
    <svg width="16" height="16" viewBox="0 0 24 24"><path fill="#ec1f27" d="M6.6 10.8a15 15 0 0 0 6.6 6.6l2.2-2.2a1 1 0 0 1 1-.25 11.4 11.4 0 0 0 3.6.57 1 1 0 0 1 1 1V20a1 1 0 0 1-1 1A17 17 0 0 1 3 4a1 1 0 0 1 1-1h3.5a1 1 0 0 1 1 1c0 1.25.2 2.45.57 3.6a1 1 0 0 1-.25 1z"/></svg>
    1300 555 014
  </div>
  <div class="search">
    <div class="search-field">SEARCH</div>
    <div class="search-btn"><svg width="18" height="18" viewBox="0 0 24 24"><circle cx="10" cy="10" r="6.5" fill="none" stroke="#fff" stroke-width="3"/><path d="M15 15l6 6" stroke="#fff" stroke-width="3" stroke-linecap="round"/></svg></div>
  </div>
</header>

<nav class="main-nav">
  <a>COUNSELLING TYPES</a><a>RELATIONSHIP COUNSELLING LOCATIONS</a><a>SEX THERAPY LOCATIONS</a><a>QUIZZES</a><a>F.A.Q.'S</a><a>CONTACT</a>
</nav>

<section class="hero" role="img" aria-label="Photo of a laughing couple outdoors, the woman riding on the man's back with arms spread"></section>
<form class="finder abs">
  <div class="finder-title">FIND OUR PSYCHOLOGIST NEAR YOU</div>
  <div class="finder-body">
    <div class="finder-field">Type of Counselling <svg width="10" height="7" viewBox="0 0 10 7"><path d="M1 1l4 4 4-4" fill="none" stroke="#333" stroke-width="1.5"/></svg></div>
    <div class="finder-field">Location</div>
    <div class="finder-or">OR</div>
    <div class="finder-field">Postcode</div>
    <div class="finder-btn">SEARCH</div>
  </div>
</form>

<h1 class="intro-title">WE SPECIALISE IN<br>RELATIONSHIP &amp; MARRIAGE COUNSELLING</h1>
<div class="intro-copy">
  <p>At the Kelvale Clinic, we are a group of PSYCHOLOGISTS, Australia wide who are passionate about relationships and helping you with yours.</p>
  <p>Our vision is to provide the most highly regarded and comprehensive marriage counselling and relationship counselling, and sex therapy in Australia, at reasonable and affordable rates.</p>
  <p>When we are experiencing relationship and marriage problems, there can be a lot of pain and confusion, and it can often be difficult to cope with the other areas of our lives when we are struggling with problems with our partner.</p>
</div>
<a class="btn-teal">READ MORE</a>

<div class="video">
  <div class="video-frame" role="img" aria-label="Video still of the clinic's lead psychologist speaking, with a couple in the background"></div>
  <div class="video-caption"><small>Head Psychologist &amp; Founder</small>ROSA LINDEN</div>
  <svg class="play" width="42" height="42" viewBox="0 0 42 42"><circle cx="21" cy="21" r="20" fill="rgba(0,0,0,.35)" stroke="#fff" stroke-width="2"/><path d="M16 12l14 9-14 9z" fill="#fff"/></svg>
  <svg class="abs" style="left:12px;top:264px" width="14" height="12" viewBox="0 0 14 12"><path d="M2 1l10 5-10 5z" fill="#aaa"/></svg>
  <div class="abs" style="left:8px;top:258px;width:454px;height:2px;background:#444"></div>
</div>

<section class="services" role="img" aria-label="Faded photo of people seated in a group therapy circle"></section>
<h2 class="section-title" style="top:1148px;color:var(--white)">OUR SERVICES</h2>

<article class="service-card" style="left:88px">
  <div class="service-photo" role="img" aria-label="Photo of a couple talking with a counsellor" style="background:linear-gradient(135deg,#c9d3dc,#8f9aa6)"></div>
  <h3>RELATIONSHIP<br>COUNSELLING</h3>
  <p>Communication, Recovering from an affair, Loss of intimacy &amp; love, Power battles, Feeling like friends, not lovers</p>
  <a class="more">Read More &gt;</a>
</article>
<article class="service-card" style="left:345px">
  <div class="service-photo" role="img" aria-label="Photo of a couple sitting apart, turned away from each other" style="background:linear-gradient(135deg,#3a3a3a,#8a8580)"></div>
  <h3>SEX THERAPY<br>COUNSELLING</h3>
  <p>Low libido , Erectile difficulties, Premature ejaculation, Differing libidos, Porn addiction, Keeping sex exciting</p>
  <a class="more">Read More &gt;</a>
</article>
<article class="service-card" style="left:605px">
  <div class="service-photo" role="img" aria-label="Photo of a couple arguing on a sofa" style="background:linear-gradient(135deg,#d8dde2,#7a8794)"></div>
  <h3>ANGER MANAGEMENT<br>COUNSELLING</h3>
  <p>As we have found that a major cause of relationship issues is poor anger management, our Kelvale Clinic Psychologists</p>
  <a class="more">Read More &gt;</a>
</article>
<article class="service-card" style="left:864px">
  <div class="service-photo" role="img" aria-label="Photo of a smug man in a suit with mocking faces behind him" style="background:linear-gradient(135deg,#5a4a3a,#3a2f25)"></div>
  <h3>NARCISSISM<br>COUNSELLING</h3>
  <p>Managing narcissistic, superior, entitled, arrogant and lack of empathy tendencies in you or your partner</p>
  <a class="more">Read More &gt;</a>
</article>

<h2 class="section-title" style="top:1745px;color:var(--ink)">LATEST NEWS</h2>

<article class="news-card" style="left:88px">
  <div class="news-photo" role="img" aria-label="Photo of a stressed woman holding her head" style="background:linear-gradient(135deg,#d9d4cf,#a49a90)">
    <div class="date teal">Apr<b>22</b>2017</div>
  </div>
  <h4>What can I do if I'm living with a Narcissist?</h4>
  <p>If you are in a relationship with a Narcissist, in his/her mind, you are an extension of him/her and he/she must always win, so his/her eruptions of temper and ego and devaluations and guilt are</p>
  <a class="more">Read More &gt;</a>
</article>
<article class="news-card" style="left:439px">
  <div class="news-photo" role="img" aria-label="Photo of an upset woman with a man turned away behind her" style="background:linear-gradient(135deg,#bfbfbf,#e6e2de)">
    <div class="date red">Apr<b>23</b>2017</div>
  </div>
  <h4 class="hot">Why am I with a Narcissist?</h4>
  <p>You may be wondering why anyone would be masochistic enough to ever get themselves into a relationship with someone who has so many characteristics of a Narcissist and who leaves you</p>
  <a class="more hot">Read More &gt;</a>
</article>
<article class="news-card" style="left:791px">
  <div class="news-photo" role="img" aria-label="Photo of a crying woman while a man shouts beside her" style="background:linear-gradient(135deg,#b89a88,#8a6f62)">
    <div class="date teal">Apr<b>24</b>2017</div>
  </div>
  <h4>How Do I Know If I'm With a Narcissist?</h4>
  <p>An integral part of a healthy relationship is a sense of equality and consideration and empathy for each other. In fact no relationship can feel rewarding and supportive if either partner is</p>
  <a class="more">Read More &gt;</a>
</article>

<footer class="site-footer">
  <div class="foot-col" style="left:86px">
    <h5>CONTACT US</h5>
    <div class="contact-line"><svg width="10" height="14" viewBox="0 0 10 14"><path d="M5 0a5 5 0 0 0-5 5c0 4 5 9 5 9s5-5 5-9a5 5 0 0 0-5-5zm0 7a2 2 0 1 1 0-4 2 2 0 0 1 0 4z" fill="#fff"/></svg>Suite 4, Level 1, 20-24 Ferris Street Marlow NSW 2290</div>
    <div class="contact-line"><svg width="12" height="12" viewBox="0 0 24 24"><path fill="#fff" d="M6.6 10.8a15 15 0 0 0 6.6 6.6l2.2-2.2a1 1 0 0 1 1-.25 11.4 11.4 0 0 0 3.6.57 1 1 0 0 1 1 1V20a1 1 0 0 1-1 1A17 17 0 0 1 3 4a1 1 0 0 1 1-1h3.5a1 1 0 0 1 1 1c0 1.25.2 2.45.57 3.6a1 1 0 0 1-.25 1z"/></svg>1300 555 014</div>
    <div class="contact-line"><svg width="13" height="10" viewBox="0 0 13 10"><rect width="13" height="10" fill="#fff"/><path d="M0 0l6.5 5L13 0" fill="none" stroke="#1b1b1b" stroke-width="1.2"/></svg>info@kelvaleclinic.com.au</div>
  </div>
  <div class="social"><span></span><span></span><span></span><span></span></div>

  <div class="foot-col" style="left:487px">
    <h5>SEND US A MESSAGE</h5>
    <div class="field" style="margin-top:14px">Name</div>
    <div class="field">Email</div>
    <div class="field tall">Message</div>
    <div class="send">SEND</div>
  </div>

  <div class="foot-col" style="left:846px">
    <h5 style="width:268px">NEWSLETTER SUBSCRIBE</h5>
    <p class="news-note">Subscribe to our newsletter and we will inform you about newest Projects.</p>
    <div class="subscribe">
      <div class="subscribe-field">Your email</div>
      <div class="subscribe-btn"><svg width="20" height="20" viewBox="0 0 24 24"><path d="M2 11L22 3l-6 18-4-7z" fill="none" stroke="#fff" stroke-width="2" stroke-linejoin="round"/><path d="M12 14l10-11" stroke="#fff" stroke-width="2"/></svg></div>
    </div>
  </div>

  <div class="bottom-bar">
    <div class="legal"><a>PRIVACY POLICY</a>|<a>TERMS &amp; CONDITIONS</a>|<a>SITE MAP</a>|<a>ASSOCIATE PSYCHOLOGISTS PROGRAM</a>|<a>CONTACT US</a></div>
    <div>Copyright © 2017. The Kelvale Clinic . All rights reserved.&nbsp;&nbsp;&nbsp;&nbsp;&nbsp;C24</div>
  </div>
</footer>

</body>
</html>
```